Real estate broker business card

Want a modern celan but effective business card for my residential and commercial real estate business. I want the back of the card to advertise my services and to capture business. I have attached the back of my current business card fore ideas
Updates

Logos, photo and text updates added! Added Saturday, September 3, 2016

Project Deadline Extended Reason: LOGOS, PHOTOS AND TEST JUST UPLOADED! I'M READY TO PICK A DESIGN! THANK YOU! Added Saturday, September 3, 2016

Target Market(s)

home buyers and seller. commercial buyers and sellers

Industry/Entity Type

Real Estate

Contact Information for Business Card

must have my contact information and my photo

Requirements
Must have
• Carla Ventrino
• Owner & Qualifying Broker
• Ventrino Real Estate Services
• 505.718.2094
• carla@ventrinohomes.example
• www.ventrinohomes.example
Nice to have
• metallic
• Business capture text: " Don't buy or lease property without someone looking out for your best interests. I will represent you on your home or investment purchase for FREE!"
• "Home owners, call today to receive a FREE market analysis for your homes value!

```html
<!DOCTYPE html>
<html lang="en">
<head>
<meta charset="utf-8">
<title>Ventrino Real Estate Services – Business Card</title>
<link rel="stylesheet" href="https://fonts.googleapis.com/css2?family=Cinzel:wght@500;600&family=Barlow+Semi+Condensed:wght@400;500&display=swap">
<style>
  :root {
    --page-bg: #1e1e1e;
    --card-white: #ffffff;
    --teal: #0e7b88;
    --teal-light: #1a96a6;
    --teal-dark: #05606c;
    --ink: #4a4a4a;
    --ink-dark: #3b3b3b;
    --silver: #e4ecee;
    --photo-dark: #1f2a1c;
    --photo-mid: #3f5a38;
  }
  * { box-sizing: border-box; margin: 0; padding: 0; }
  html, body {
    width: 1200px;
    height: 987px;
    overflow: hidden;
    background: var(--page-bg);
  }
  .canvas {
    position: relative;
    width: 1200px;
    height: 987px;
  }
  .card {
    position: absolute;
    left: 293px;
    width: 615px;
    height: 352px;
    overflow: hidden;
  }
  .card--front { top: 130px; background: var(--card-white); }
  .card--back {
    top: 505px;
    background: radial-gradient(ellipse at 50% 45%, var(--teal-light) 0%, var(--teal) 45%, var(--teal-dark) 100%);
  }

  /* Brand lockup */
  .brand-mark {
    position: absolute;
    left: 37px;
    top: 30px;
    width: 56px;
    height: 56px;
    background: var(--teal);
  }
  .brand-name {
    position: absolute;
    left: 108px;
    top: 36px;
    font-family: "Cinzel", serif;
    font-weight: 600;
    font-size: 40px;
    line-height: 1;
    color: var(--teal);
    letter-spacing: 1px;
  }
  .brand-tagline {
    position: absolute;
    left: 110px;
    top: 80px;
    font-family: "Barlow Semi Condensed", sans-serif;
    font-weight: 500;
    font-size: 11.5px;
    letter-spacing: 2.6px;
    color: var(--ink-dark);
  }

  /* Person */
  .person-name {
    position: absolute;
    left: 38px;
    top: 128px;
    font-family: "Cinzel", serif;
    font-weight: 600;
    font-size: 25px;
    line-height: 1;
    color: var(--teal);
  }
  .person-role {
    position: absolute;
    left: 38px;
    top: 156px;
    font-family: "Barlow Semi Condensed", sans-serif;
    font-size: 16px;
    line-height: 21px;
    color: var(--ink);
    text-transform: uppercase;
  }

  /* Contact list */
  .contact-list {
    position: absolute;
    left: 38px;
    top: 211px;
    list-style: none;
    font-family: "Barlow Semi Condensed", sans-serif;
    font-size: 16px;
    color: var(--ink);
  }
  .contact-list li {
    display: flex;
    align-items: center;
    height: 24.5px;
  }
  .contact-list svg {
    width: 15px;
    height: 15px;
    margin-right: 9px;
    fill: var(--teal);
  }
  .contact-list .upper { text-transform: uppercase; }

  .portrait {
    position: absolute;
    left: 373px;
    top: 37px;
    width: 200px;
    height: 243px;
    border-radius: 10px;
    background: radial-gradient(ellipse at 55% 60%, #c9b8aa 0%, #7d6a5c 30%, var(--photo-mid) 60%, var(--photo-dark) 100%);
  }

  .divider {
    position: absolute;
    left: 0;
    top: 302px;
    width: 100%;
    height: 3px;
    background: var(--teal);
  }
  .offer {
    position: absolute;
    left: 0;
    top: 305px;
    width: 100%;
    height: 47px;
    display: flex;
    align-items: center;
    justify-content: center;
    font-family: "Barlow Semi Condensed", sans-serif;
    font-weight: 500;
    font-size: 15px;
    color: var(--ink-dark);
    text-transform: uppercase;
  }

  .back-name {
    position: absolute;
    inset: 0;
    display: flex;
    align-items: center;
    justify-content: center;
    font-family: "Cinzel", serif;
    font-weight: 600;
    font-size: 46px;
    letter-spacing: 3px;
    color: var(--silver);
  }
</style>
</head>
<body>
<main class="canvas">
  <section class="card card--front">
    <div class="brand-mark"></div>
    <div class="brand-name">VENTRINO</div>
    <div class="brand-tagline">REAL ESTATE SERVICES</div>

    <h1 class="person-name">Carla Ventrino</h1>
    <p class="person-role">Owner &amp; Qualifying Broker<br>Ventrino Real Estate Services</p>

    <ul class="contact-list">
      <li>
        <svg viewBox="0 0 24 24" aria-hidden="true"><path d="M6.6 10.8c1.4 2.8 3.8 5.1 6.6 6.6l2.2-2.2c.3-.3.7-.4 1-.2 1.1.4 2.3.6 3.6.6.6 0 1 .4 1 1V20c0 .6-.4 1-1 1C10.6 21 3 13.4 3 4c0-.6.4-1 1-1h3.5c.6 0 1 .4 1 1 0 1.3.2 2.5.6 3.6.1.3 0 .7-.2 1L6.6 10.8z"/></svg>
        505.718.2094
      </li>
      <li>
        <svg viewBox="0 0 24 24" aria-hidden="true"><path d="M2 5h20v14H2z M2 5l10 8 10-8" fill="none" stroke="#0e7b88" stroke-width="0"/><path d="M2 6.5V19h20V6.5l-10 7.5L2 6.5zM2.8 5h18.4L12 11.8 2.8 5z"/></svg>
        <span class="upper">carla@ventrinohomes.example</span>
      </li>
      <li>
        <svg viewBox="0 0 24 24" aria-hidden="true"><circle cx="12" cy="12" r="10"/><path d="M4 10c3 0 4 2 6 2s1 4 3 5-1 4-1 4M14 3c0 2 2 3 4 3s2 3 4 4" fill="none" stroke="#fff" stroke-width="1.8"/></svg>
        <span class="upper">www.ventrinohomes.example</span>
      </li>
    </ul>

    <div class="portrait" role="img" aria-label="Portrait photograph of the broker"></div>

    <div class="divider"></div>
    <p class="offer">Home owners, call today to receive a free market analysis for your homes value!</p>
  </section>

  <section class="card card--back">
    <div class="back-name">VENTRINO</div>
  </section>
</main>
</body>
</html>
```